Modern Business Card

Modern professional business card with more than just logo and demographic info. Something memorable.

We are a trendy/modern chiropractic group with an emphasis on neurology, hence the minimalist-type brain logo. We want to convey that modern and technical aspect with professionalism and the elite nature of our practice environment.

```html
<!DOCTYPE html>
<html lang="en">
<head>
<meta charset="utf-8">
<title>Meridian Chiropractic — Business Card</title>
<link href="https://fonts.googleapis.com/css2?family=Tinos:wght@400;700&family=Montserrat:wght@400;500&display=swap" rel="stylesheet">
<style>
  :root {
    --backdrop: #2b2b2c;
    --card: #1b1b1c;
    --card-edge: #232324;
    --ink: #ffffff;
    --muted: #d8d8d8;
    --accent: #3d7cc9;
    --pattern-dark: #161617;
    --pattern-light: #2c2c2e;
  }
  * { box-sizing: border-box; margin: 0; padding: 0; }
  html, body {
    width: 1200px; height: 900px; overflow: hidden;
    background: var(--backdrop);
  }
  .stage {
    position: relative; width: 1200px; height: 900px;
    display: flex; flex-direction: column; align-items: center;
    justify-content: center; gap: 40px;
  }
  .card {
    position: relative; width: 700px; height: 400px;
    border-radius: 22px; background: var(--card);
    overflow: hidden;
    box-shadow: 0 14px 30px rgba(0,0,0,.45);
  }
  /* back */
  .card-back .texture {
    position: absolute; inset: 0;
    background: linear-gradient(115deg, var(--pattern-dark) 0%, #1e1e20 45%, var(--pattern-light) 100%);
  }
  .card-back .brand-mark {
    position: absolute; right: 70px; bottom: 110px;
    font-family: "Tinos", serif; font-weight: 400;
    color: var(--ink); letter-spacing: 1px; line-height: 1;
    text-align: left;
  }
  .brand-mark .line-1 { display: block; font-size: 30px; }
  .brand-mark .line-2 { display: block; font-size: 16px; letter-spacing: 1.5px; }

  /* front */
  .card-front .wordmark {
    position: absolute; left: 52px; top: 42px;
    font-family: "Tinos", serif; font-weight: 400;
    color: var(--ink); line-height: .9;
  }
  .wordmark .line-1 { display: block; font-size: 64px; letter-spacing: 1px; }
  .wordmark .line-2 { display: block; font-size: 38px; letter-spacing: 1.5px; }

  .person {
    position: absolute; left: 52px; top: 178px;
  }
  .person .name {
    font-family: "Tinos", serif; font-weight: 700; font-size: 32px;
    color: var(--ink); letter-spacing: .5px; line-height: 1;
  }
  .person .name .first { color: var(--accent); }
  .person .role {
    font-family: "Montserrat", sans-serif; font-size: 17px;
    color: var(--muted); margin-top: 6px;
  }
  .rule {
    position: absolute; left: 165px; right: 55px; top: 240px;
    height: 1.5px; background: var(--accent);
  }
  .badge {
    position: absolute; left: 52px; top: 268px;
    display: flex; align-items: center; gap: 10px;
  }
  .badge .dot { width: 26px; height: 26px; border-radius: 50%; background: var(--accent); }
  .badge .name {
    font-family: "Tinos", serif; font-weight: 400; font-size: 20px;
    color: var(--accent); letter-spacing: 1px;
  }
  .contact {
    position: absolute; left: 52px; top: 312px;
    list-style: none;
    font-family: "Montserrat", sans-serif; font-size: 18px; color: var(--ink);
  }
  .contact li { display: flex; align-items: center; gap: 12px; height: 26px; }
  .contact svg { width: 16px; height: 16px; fill: none; stroke: var(--accent); stroke-width: 1.6; }
  .address {
    position: absolute; right: 55px; bottom: 40px;
    font-family: "Montserrat", sans-serif; font-size: 18px;
    color: var(--ink); line-height: 1.35; font-style: normal;
  }
</style>
</head>
<body>
<main class="stage">
  <section class="card card-back">
    <div class="texture" role="img" aria-label="Tonal repeating brand pattern across the card back"></div>
    <div class="brand-mark">
      <span class="line-1">MERIDIAN</span>
      <span class="line-2">CHIROPRACTIC</span>
    </div>
  </section>

  <section class="card card-front">
    <div class="wordmark">
      <span class="line-1">MERIDIAN</span>
      <span class="line-2">CHIROPRACTIC</span>
    </div>

    <div class="person">
      <p class="name"><span class="first">DANIEL</span> BROOKS</p>
      <p class="role">Director</p>
    </div>
    <div class="rule"></div>

    <div class="badge"><span class="dot"></span><span class="name">MERIDIAN</span></div>

    <ul class="contact">
      <li>
        <svg viewBox="0 0 16 16"><path d="M4 1.5l2.5 3-1.5 1.5a8 8 0 0 0 5 5l1.5-1.5 3 2.5-1.5 2.5C7 14.5 1.5 9 1.5 3z"/></svg>
        (541) 555-0148
      </li>
      <li>
        <svg viewBox="0 0 16 16"><rect x="1.5" y="3.5" width="13" height="9" rx="1"/><path d="M1.5 4l6.5 5 6.5-5"/></svg>
        info@meridianchiro.com
      </li>
      <li>
        <svg viewBox="0 0 16 16"><circle cx="8" cy="8" r="6.5"/><path d="M1.5 8h13M8 1.5c-3 3.5-3 9.5 0 13M8 1.5c3 3.5 3 9.5 0 13"/></svg>
        www.meridianchiro.com
      </li>
    </ul>

    <address class="address">
      1187 Cedar Bend Road<br>
      Salem, OR 97302
    </address>
  </section>
</main>
</body>
</html>
```